business card for a massage therapy practice named 'Cedar and Willow Massage Studio'

I really need a trendy, yet easy on the eyes business card to complement my logo. Ideally with some gold or rose gold foil work.

My uploaded file of the logo I have in horizontal but I have a vertical version as well. Another color that is used in the website is a blush pink here and there. I'd like to see some trendy tropical leaves in the design.

```html
<!DOCTYPE html>
<html lang="en">
<head>
<meta charset="utf-8">
<title>Cedar and Willow Massage Studio — Business Card</title>
<link rel="stylesheet" href="https://fonts.googleapis.com/css2?family=Amatic+SC:wght@700&family=Questrial&display=swap">
<style>
  :root {
    --backdrop: #e4e4e6;
    --card-white: #fbfbf9;
    --gold: #94805a;
    --gold-soft: #c9bb9c;
    --gold-pale: #ece5d6;
    --ink-grey: #6f6f6f;
    --white: #ffffff;
  }
  html, body {
    margin: 0;
    padding: 0;
    width: 1200px;
    height: 857px;
    overflow: hidden;
    background: var(--backdrop);
  }
  .canvas {
    position: relative;
    width: 1200px;
    height: 857px;
  }
  .card {
    position: absolute;
    top: 280px;
    width: 520px;
    height: 297px;
    overflow: hidden;
    box-shadow: 0 6px 18px rgba(0,0,0,0.14);
  }
  .card--front { left: 60px; background: var(--card-white); }
  .card--back  { left: 620px; background: var(--gold); }

  /* front */
  .pattern-field {
    position: absolute;
    left: 0; top: 0;
    width: 520px; height: 150px;
    background: linear-gradient(160deg, var(--gold-pale) 0%, var(--gold-soft) 55%, var(--gold-pale) 100%);
  }
  .contact {
    position: absolute;
    left: 280px; top: 170px;
    font-family: "Questrial", sans-serif;
    font-size: 13px;
    line-height: 16px;
    color: var(--ink-grey);
    letter-spacing: 0.3px;
  }
  .person {
    position: absolute;
    left: 34px; top: 218px;
  }
  .person__name {
    font-family: "Amatic SC", cursive;
    font-weight: 700;
    font-size: 30px;
    line-height: 30px;
    color: var(--gold);
    letter-spacing: 1px;
  }
  .person__role {
    font-family: "Questrial", sans-serif;
    font-size: 13px;
    color: var(--ink-grey);
    letter-spacing: 1.5px;
    text-transform: uppercase;
  }

  /* back */
  .brand {
    position: absolute;
    left: 70px; top: 108px;
    display: flex;
    align-items: center;
    gap: 16px;
  }
  .brand__mark {
    width: 44px; height: 44px;
    flex: none;
  }
  .brand__name {
    font-family: "Questrial", sans-serif;
    font-size: 26px;
    line-height: 32px;
    color: var(--white);
    letter-spacing: 1px;
  }
  .website {
    position: absolute;
    left: 0; right: 0; top: 238px;
    text-align: center;
    font-family: "Questrial", sans-serif;
    font-size: 14px;
    color: var(--white);
    letter-spacing: 1px;
  }
</style>
</head>
<body>
<main class="canvas">

  <section class="card card--front" aria-label="Business card front">
    <div class="pattern-field" role="img" aria-label="Scattered gold tropical fruit pattern"></div>
    <div class="contact">
      310.555.0142<br>
      mara@CedarWillowStudio.com<br>
      www.CedarWillowStudio.com
    </div>
    <div class="person">
      <div class="person__name">MARA ELLISON</div>
      <div class="person__role">Consultant</div>
    </div>
  </section>

  <section class="card card--back" aria-label="Business card back">
    <div class="brand">
      <svg class="brand__mark" viewBox="0 0 44 44" aria-hidden="true">
        <circle cx="22" cy="22" r="20" fill="var(--white)"/>
      </svg>
      <div class="brand__name">Cedar and Willow<br>Massage Studio</div>
    </div>
    <div class="website">www.cedarwillowmassage.com</div>
  </section>

</main>
</body>
</html>
```